Group training gym/bootcamp needs a web design

We need a website for our gym that is based in Sydney. We have indoor functional training classes and outdoor bootcamp classes. We would like the web site to have a video (to be created) and photo gallery. I would like the site made on word press and i would like to be able to make minor changes such as changing images and text without having to use a designer.

The website should have the following pages: home page; the gym; the bootcamp; photo gallery; about us; contact.

I have uploaded our logo and i would like to keep to these colour (blue,yellow,silver) and black is also allowed

Target Market(s)

18-50 male and female

Industry/Entity Type

Gym

Coding

Coded - Design and coding required

Number of Pages Required

5+ page

Font styles to use
Sans Serif

Colors
0692cd
fbed22
1b1b1b
e8e8e8

Requirements
Must have
• The website should have the following pages: home page; the gym; the bootcamp; photo gallery; about us; contact.
• I have uploaded our logo and i would like to keep to these colour (blue,yellow,silver) and black is also allowed
• Video upload and photo upload

```html
<!DOCTYPE html>
<html lang="en">
<head>
<meta charset="utf-8">
<title>Ironbark Fitness Hub</title>
<link href="https://fonts.googleapis.com/css2?family=Oswald:wght@400;500;600&family=Open+Sans:wght@400;600&display=swap" rel="stylesheet">
<style>
:root{
  --blue:#0692cd;
  --blue-deep:#0a6fb4;
  --yellow:#fbed22;
  --black:#1b1b1b;
  --silver:#e8e8e8;
  --white:#ffffff;
  --grey-text:#9a9a9a;
  --header:#2e2e2e;
}
*{margin:0;padding:0;box-sizing:border-box}
html,body{width:1200px;height:4196px;overflow:hidden}
body{position:relative;background:var(--white);font-family:'Open Sans',sans-serif;color:var(--black)}
.abs{position:absolute}
.heading{font-family:'Oswald',sans-serif;font-weight:500;text-transform:uppercase;color:var(--blue-deep)}
.btn{position:absolute;display:flex;align-items:center;justify-content:center;font-family:'Oswald',sans-serif;font-weight:500;text-transform:uppercase;letter-spacing:.5px}
.btn-yellow{background:var(--yellow);color:var(--white)}
.btn-blue{background:var(--blue-deep);color:var(--white)}

/* header */
.site-header{left:0;top:0;width:1200px;height:154px;background:var(--header);z-index:10}
.social{display:flex;gap:8px}
.social span{width:16px;height:16px;border-radius:50%;background:var(--white);opacity:.85}
.social span:first-child{background:var(--blue)}
.header-social{left:224px;top:64px}
.brand{display:flex;align-items:center;gap:8px;font-family:'Oswald',sans-serif;font-weight:600;text-transform:uppercase;color:var(--yellow)}
.brand .mark{width:26px;height:26px;background:var(--blue)}
.header-brand{left:520px;top:54px;font-size:22px}
.header-phone{left:836px;top:62px;color:var(--white);font-family:'Oswald',sans-serif;font-size:17px;display:flex;align-items:center;gap:8px}
.main-nav{left:230px;top:122px;width:735px;height:63px;background:var(--blue-deep);display:flex;align-items:center;z-index:11}
.main-nav a{font-family:'Oswald',sans-serif;font-weight:500;font-size:17px;line-height:1;color:var(--white);text-decoration:none;text-transform:uppercase;padding:0 14px;height:100%;display:flex;align-items:center;white-space:nowrap}
.main-nav a.active{background:var(--yellow);padding:0 34px}

/* hero */
.hero{left:0;top:154px;width:1200px;height:559px;background:linear-gradient(90deg,#0d0d0d 0%,#3a322b 45%,#5a4a3c 60%,#161616 100%);z-index:1;overflow:hidden}
.hero-photo{left:220px;top:0;width:780px;height:559px;background:radial-gradient(ellipse at 60% 40%,rgba(140,115,90,.6),rgba(20,20,20,0) 70%)}
.hero-shape{background:rgba(251,237,34,.72)}
.hero-shape.one{left:228px;top:150px;width:220px;height:230px;transform:rotate(-8deg)}
.hero-shape.two{left:214px;top:176px;width:236px;height:190px;transform:rotate(6deg);background:rgba(251,237,34,.5)}
.hero-title{left:254px;top:184px;font-family:'Oswald',sans-serif;font-weight:400;font-size:48px;line-height:56px;color:var(--white);text-transform:uppercase}
.hero-btn{left:255px;top:392px;width:153px;height:50px;font-size:18px}
.hero-dots{left:1130px;top:222px;display:flex;flex-direction:column;gap:12px}
.hero-dots span{width:9px;height:9px;border-radius:50%;background:var(--white)}
.hero-dots span:first-child{background:var(--blue)}

/* welcome */
.welcome{left:0;top:713px;width:1200px;height:616px;background:linear-gradient(180deg,#f7f7f7,#ffffff)}
.welcome-title{left:243px;top:108px;font-size:42px;line-height:52px}
.welcome-title .accent{color:var(--yellow)}
.welcome-body{left:243px;top:246px;width:320px;font-size:14.5px;line-height:28px;color:var(--grey-text)}
.welcome-photo{left:660px;top:30px;width:490px;height:586px;background:radial-gradient(ellipse at 50% 60%,#9ea6b2 0%,#d8dce2 45%,rgba(255,255,255,0) 72%)}

/* feature bands */
.band{left:0;width:1200px;height:567px}
.band-gym{top:1329px;background:linear-gradient(90deg,#2b2420,#4a3a30 50%,#2a2624)}
.band-boot{top:2624px;height:570px;background:linear-gradient(90deg,#6a4a38,#8d6a52 45%,#3f4660 100%)}
.band-overlay{left:0;top:0;width:100%;height:100%;background:rgba(20,20,20,.55)}
.band-title{left:0;width:1200px;text-align:center;font-size:42px}
.band-body{left:220px;width:760px;text-align:center;font-size:15px;line-height:30px;color:var(--white)}
.band-btn{left:523px;width:154px;height:54px;font-size:18px}

/* videos */
.videos-title{left:0;top:1972px;width:1200px;text-align:center;font-size:42px}
.video-card{top:2089px;width:224px;height:420px;background:var(--blue-deep)}
.video-thumb{left:0;top:0;width:224px;height:210px}
.play{left:82px;top:75px;width:60px;height:60px;background:var(--blue-deep);display:flex;align-items:center;justify-content:center}
.video-name{left:12px;top:232px;font-family:'Oswald',sans-serif;font-weight:500;font-size:21px;color:var(--white)}
.video-text{left:12px;top:276px;width:200px;font-size:9.5px;line-height:15px;color:var(--white)}
.video-btn{left:12px;top:364px;width:108px;height:38px;font-size:12px}

/* gallery */
.gallery-title{left:0;top:3272px;width:1200px;text-align:center;font-size:42px}
.gallery-cell{width:234px;height:207px}
.gallery-intro{background:var(--blue);display:flex;flex-direction:column;align-items:center;justify-content:center;gap:10px}
.gallery-intro .brand{font-size:15px;color:var(--white)}
.gallery-intro .brand .mark{background:var(--white);width:20px;height:20px}
.gallery-intro p{width:150px;text-align:center;font-size:9px;line-height:13px;color:var(--white)}

/* footer */
.site-footer{left:0;top:3874px;width:1200px;height:322px;background:#f6f6f6}
.footer-brand{left:0;top:72px;width:1200px;justify-content:center;font-size:24px;color:var(--blue-deep)}
.footer-brand .mark{background:var(--yellow)}
.footer-social{left:0;top:172px;width:1200px;justify-content:center;gap:12px}
.footer-social span{width:22px;height:22px;background:var(--blue-deep);opacity:1}
.footer-social span:first-child{background:var(--blue)}
.footer-nav{left:0;top:220px;width:1200px;display:flex;justify-content:center;gap:30px}
.footer-nav a{font-family:'Oswald',sans-serif;font-size:13px;color:var(--black);text-decoration:none;text-transform:uppercase}
.copyright{left:0;top:262px;width:1200px;text-align:center;font-family:'Oswald',sans-serif;font-size:12px;color:var(--black)}
</style>
</head>
<body>

<header class="abs site-header">
  <div class="abs social header-social"><span></span><span></span><span></span><span></span><span></span><span></span></div>
  <div class="abs brand header-brand"><span class="mark"></span>Ironbark</div>
  <div class="abs header-phone">
    <svg width="14" height="14" viewBox="0 0 24 24"><path fill="#fbed22" d="M6.6 10.8a15 15 0 0 0 6.6 6.6l2.2-2.2a1 1 0 0 1 1-.25 11.4 11.4 0 0 0 3.6.57 1 1 0 0 1 1 1V20a1 1 0 0 1-1 1A17 17 0 0 1 3 4a1 1 0 0 1 1-1h3.5a1 1 0 0 1 1 1c0 1.25.2 2.450.57 3.57a1 1 0 0 1-.25 1z"/></svg>
    1-800-555-0147
  </div>
  <nav class="abs main-nav">
    <a class="active" href="#">Home</a><a href="#">The Gym</a><a href="#">The Bootcamp</a><a href="#">Photo Gallery</a><a href="#">About Us</a><a href="#">Contact Us</a>
  </nav>
</header>

<section class="abs hero">
  <div class="abs hero-photo" role="img" aria-label="Group of athletes doing lunges in an indoor training studio"></div>
  <div class="abs hero-shape two"></div>
  <div class="abs hero-shape one"></div>
  <h1 class="abs hero-title">Indoor<br>Functional<br>Training</h1>
  <a class="btn btn-blue hero-btn">Book Now</a>
  <div class="abs hero-dots"><span></span><span></span><span></span><span></span></div>
</section>

<section class="abs welcome">
  <div class="abs welcome-photo" role="img" aria-label="Man sitting on an exercise ball lifting dumbbells"></div>
  <h2 class="abs heading welcome-title">Welcome to Ironbark<br><span class="accent">Fitness Hub</span></h2>
  <p class="abs welcome-body">Sed ut perspiciatis unde omnis iste natus error sit voluptatem accusantium doloremque laudantium, totam rem aperiam, eaque ipsa quae ab illo inventore veritatis et quasi architecto beatae vitae dicta sunt explicabo. Nemo enim ipsam voluptatem quia voluptas sit aspernatur aut odit aut fugit, sed quia consequuntur</p>
</section>

<section class="abs band band-gym" role="img" aria-label="Athletes training with weights in the gym">
  <div class="abs band-overlay"></div>
  <h2 class="abs heading band-title" style="top:124px;color:var(--blue)">The Gym</h2>
  <p class="abs band-body" style="top:202px">Sed ut perspiciatis unde omnis iste natus error sit voluptatem accusantium doloremque laudantium, totam rem aperiam, eaque ipsa quae ab illo inventore veritatis et quasi architect Sed ut perspiciatis unde omnis iste natus error sit voluptatem accusantium doloremque laudantium, totam rem aperiam, eaque ipsa quae ab illo inventore veritatis et quasi architecto beatae vitae dicta sunt explicabo. Nemo enim ipsam voluptatem quia voluptas sit aspernatur aut odit aut fugit, sed quia</p>
  <a class="btn btn-yellow band-btn" style="top:394px">Learn More</a>
</section>

<h2 class="abs heading videos-title">Videos</h2>

<article class="abs video-card" style="left:243px">
  <div class="abs video-thumb" role="img" aria-label="Couple training with dumbbells" style="background:linear-gradient(135deg,#d9d9d9,#8a8a8a)"></div>
  <div class="abs play"><svg width="22" height="24" viewBox="0 0 22 24"><path fill="#fff" d="M2 1l19 11L2 23z"/></svg></div>
  <h3 class="abs video-name">VIDEOS 1</h3>
  <p class="abs video-text">Sed ut perspiciatis unde omnis iste natus error sit voluptatem accusantium doloremque laudantium, totam rem aperiam.</p>
  <a class="btn btn-yellow video-btn">Watch Now</a>
</article>
<article class="abs video-card" style="left:488px">
  <div class="abs video-thumb" role="img" aria-label="Man doing a cable workout" style="background:linear-gradient(135deg,#b0603a,#3a2418)"></div>
  <div class="abs play"><svg width="22" height="24" viewBox="0 0 22 24"><path fill="#fff" d="M2 1l19 11L2 23z"/></svg></div>
  <h3 class="abs video-name">VIDEOS 2</h3>
  <p class="abs video-text">Sed ut perspiciatis unde omnis iste natus error sit voluptatem accusantium doloremque laudantium, totam rem aperiam.</p>
  <a class="btn btn-yellow video-btn">Watch Now</a>
</article>
<article class="abs video-card" style="left:730px">
  <div class="abs video-thumb" role="img" aria-label="Woman stretching on a mat" style="background:linear-gradient(135deg,#e89a6a,#7a4fa0)"></div>
  <div class="abs play"><svg width="22" height="24" viewBox="0 0 22 24"><path fill="#fff" d="M2 1l19 11L2 23z"/></svg></div>
  <h3 class="abs video-name">VIDEOS 3</h3>
  <p class="abs video-text">Sed ut perspiciatis unde omnis iste natus error sit voluptatem accusantium doloremque laudantium, totam rem aperiam.</p>
  <a class="btn btn-yellow video-btn">Watch Now</a>
</article>

<section class="abs band band-boot" role="img" aria-label="Woman doing outdoor bootcamp exercises on a mat">
  <div class="abs band-overlay" style="background:rgba(20,20,20,.45)"></div>
  <h2 class="abs heading band-title" style="top:110px;color:var(--blue)">The Bootcamp</h2>
  <p class="abs band-body" style="top:188px">Sed ut perspiciatis unde omnis iste natus error sit voluptatem accusantium doloremque laudantium, totam rem aperiam, eaque ipsa quae ab illo inventore veritatis et quasi architect Sed ut perspiciatis unde omnis iste natus error sit voluptatem accusantium doloremque laudantium, totam rem aperiam, eaque ipsa quae ab illo inventore veritatis et quasi architecto beatae vitae dicta sunt explicabo. Nemo enim ipsam voluptatem quia voluptas sit aspernatur aut odit aut fugit, sed quia</p>
  <a class="btn btn-yellow band-btn" style="top:397px">Learn More</a>
</section>

<h2 class="abs heading gallery-title">Photo Gallery</h2>

<div class="abs gallery-cell gallery-intro" style="left:243px;top:3379px">
  <div class="brand"><span class="mark"></span>Ironbark</div>
  <p>Sed ut perspiciatis unde omnis iste natus error</p>
</div>
<div class="abs gallery-cell" style="left:480px;top:3379px;background:linear-gradient(135deg,#3a2a26,#8a4a40)" role="img" aria-label="Woman training with battle ropes"></div>
<div class="abs gallery-cell" style="left:717px;top:3379px;background:linear-gradient(135deg,#2a2a2a,#6a6a6a)" role="img" aria-label="Woman resting on gym equipment"></div>
<div class="abs gallery-cell" style="left:243px;top:3589px;background:linear-gradient(135deg,#e0c7a8,#b08a6a)" role="img" aria-label="Group aerobics class with steps"></div>
<div class="abs gallery-cell" style="left:480px;top:3589px;background:linear-gradient(135deg,#8a4a7a,#d08a4a)" role="img" aria-label="Group doing squats in a studio"></div>
<div class="abs gallery-cell" style="left:717px;top:3589px;background:linear-gradient(135deg,#6a8aa0,#c0c8d0)" role="img" aria-label="Woman lifting a dumbbell"></div>

<footer class="abs site-footer">
  <div class="abs brand footer-brand"><span class="mark"></span>Ironbark</div>
  <div class="abs social footer-social"><span></span><span></span><span></span><span></span><span></span><span></span></div>
  <nav class="abs footer-nav"><a href="#">Home</a><a href="#">The Gym</a><a href="#">The Bootcamp</a><a href="#">Photo Gallery</a><a href="#">About Us</a><a href="#">Contact Us</a></nav>
  <p class="abs copyright">© 2017 COMPANY NAME &nbsp;|&nbsp; ALL RIGHTS RESERVED</p>
</footer>

</body>
</html>
```